Clear Plastic Card Design

I am looking to have a business card designed from my logo icon. I am looking to match the style of a different business card I have attached in the files.
Looking for a card that is plastic, with layers of transparency in the shape of my logo icon (also attached in the files) - not a circle like the other card. The winning design will incorporate the red icon logo on the front and back and include the charity's name, "Light for the Weary Souls" in the same or similar font, as well as an email and phone number. For now, use the email: email@lightfortheweary-mail.org and the phone number 555-382-7194.
We like how the sample business card has transparency, partial and full opacity layers and a matching color scheme. Files will need to be in vector so that our business card printing company can work with it.
UPDATE:
We've some excellent designs in, thank you everyone! I got an early review from the owner, and he requested a minor redirect to find his perfect design. He wants the design to stand out by NOT being a rectangle. Try instead a circle, square, or best yet - something that falls in the outline of the logo icon, either fully or partially. Thank you, everyone!
Light for the Weary Souls text should be incorporated as well as a phone and email.

```html
<!DOCTYPE html>
<html lang="en">
<head>
<meta charset="utf-8">
<title>Light for the Weary Souls – Round Clear Card</title>
<link rel="stylesheet" href="https://fonts.googleapis.com/css2?family=Questrial&family=Roboto+Condensed:wght@300&display=swap">
<style>
  :root {
    --backdrop: #d9d2c8;
    --card-clear: #f4f2ef;
    --card-edge: #c9c4be;
    --brand-red: #b51d17;
    --band-red-light: #9c1f22;
    --band-red-dark: #5e0b0d;
    --ink: #1a1a1a;
    --contact-ink: #f1dede;
  }
  * { margin: 0; padding: 0; box-sizing: border-box; }
  html, body {
    width: 1200px;
    height: 969px;
    overflow: hidden;
    background: var(--backdrop);
  }
  .canvas {
    position: relative;
    width: 1200px;
    height: 969px;
  }
  .card-shape {
    position: absolute;
    left: 0;
    top: 0;
  }
  .org-name {
    position: absolute;
    right: 578px;
    top: 402px;
    font-family: "Questrial", sans-serif;
    font-size: 28px;
    line-height: 30px;
    color: var(--ink);
    text-align: left;
    white-space: nowrap;
  }
  .contact {
    position: absolute;
    left: 358px;
    width: 524px;
    top: 562px;
    font-family: "Roboto Condensed", sans-serif;
    font-weight: 300;
    font-size: 22px;
    line-height: 28px;
    color: var(--contact-ink);
    text-align: center;
  }
</style>
</head>
<body>
<main class="canvas">
  <svg class="card-shape" width="1200" height="969" viewBox="0 0 1200 969" aria-hidden="true">
    <defs>
      <linearGradient id="band-gradient" x1="0" y1="0" x2="1" y2="1">
        <stop offset="0" stop-color="var(--band-red-light)"/>
        <stop offset="0.5" stop-color="#8a1416"/>
        <stop offset="1" stop-color="var(--band-red-dark)"/>
      </linearGradient>
      <clipPath id="upper-half"><rect x="0" y="0" width="1200" height="494"/></clipPath>
      <clipPath id="lower-half"><rect x="0" y="494" width="1200" height="475"/></clipPath>
    </defs>
    <!-- clear disc -->
    <circle cx="620" cy="492" r="262" fill="var(--card-clear)" stroke="var(--card-edge)" stroke-width="3"/>
    <!-- red lower band -->
    <circle cx="620" cy="492" r="261" fill="url(#band-gradient)" clip-path="url(#lower-half)"/>
    <!-- inner ring -->
    <circle cx="620" cy="492" r="244" fill="none" stroke="var(--brand-red)" stroke-width="2.5" clip-path="url(#upper-half)"/>
    <circle cx="620" cy="492" r="244" fill="none" stroke="#e9dcdc" stroke-width="2.5" clip-path="url(#lower-half)"/>
    <!-- plain brand square -->
    <rect class="brand-square" x="640" y="318" width="120" height="120" fill="var(--brand-red)"/>
  </svg>

  <p class="org-name">Light for the<br>Weary Souls</p>

  <div class="contact">
    <p class="contact-phone">555-382-7194</p>
    <p class="contact-email">email@lightfortheweary-mail.org</p>
    <p class="contact-web">www.lightfortheweary-souls.org</p>
  </div>
</main>
</body>
</html>
```